Neues Etikett für Wasch- und Reinigungspaste
Zielgruppe
KAVIMOR, das sind wir, Spezialisten in Hygiene und Gastronomiebedarf. Wir stellen Reinigungsmittel im oberösterreichischen Mühlviertel (Aigen-Schlägl) her und wir beraten, planen und bieten die komplette Einrichtung von Gastronomieküchen an.
Unsere Hygieneprodukte tragen dazu bei, dass sich Menschen in einem Gebäude wohl fühlen. Denn Sauberkeit und Hygiene sind Faktoren, die für unsere Gesundheit wichtig sind. Die Zielgruppen im Bereich Reinigungsmittel sind Eigenheimbesitzer, Wohnraum-Mieter und in Betrieben das Reinigungspersonal bzw. die verantworlichen Mitarbeiter für die Objekthygiene.
Aufgabenstellung
Kurz: Wir suchen für ein altes Produkt ein neues Etikett. Das Produkt heißt „Rutosan“ und ist eine Wasch- und Reinigungspaste / Schmierseife, also ein altbewährtes Hausmittel, dass auch heute noch wunderbar vielseitig einsetzbar ist. Wir möchten ihr Image gerne etwas aufpeppen, da es unserer Meinung nach im Allgemeinen und auch bei uns zu stiefmütterlich auftritt. Wir denken, dass sie mehr in den Mittelpunkt rücken sollte, gerade da sie in vielen Fällen andere Reinigungsmittel ersetzen kann und auch durch ihre Ergiebigkeit die Umwelt entlastet.
Wir haben uns bewusst dazu entschieden, das alte Etikett hier nicht mit hochzuladen, daß heißt hier soll es keinen Wiedererkennungswert zu anderen Kavimor-Produkten geben. Bitte orientieren Sie sich allein an diesem Briefing.
Das Produkt ist sehr nachhaltig, ergiebig und damit sparsam. Erhältlich ist es in einem weißen, runden 5 kg Eimer (siehe Upload). Das Endformat des Etiketts auf dem weissen Eimer beträgt maximal 150 mm (H) x 170 mm (B). Es ist auch in kleineren und größeren Einheiten erhältlich, jedoch wird das Etikett dann durch uns angepasst.
Es ist wichtig, dass auf den ersten Blick sichtbar ist, dass es sich um eine Wasch- und Reinigungspaste handelt. Sie reinigt zum Beispiel Geschirr, Besteck, Aluminium, Glas, lackierte Möbel, Kunststoffmöbel, Fliesen, Waschbecken, Badewannen, Fahrzeuge, Maschinen, schmierige Hände, Holz- und Kunststoffböden, Feinwäsche, Wolle, Seide, Vorhänge, zum Einweichen und Vorwaschen von Arbeits- und Buntwäsche. Anwendung: 1 Esslöffel auf 10 Liter Wasser oder auch pur anwendbar je nach Einsatzbereich. Enthält keine Phosphate und ist biologisch abbaubar. Inhalt: 5 kg

```html
<!DOCTYPE html>
<html lang="de">
<head>
<meta charset="utf-8">
<title>Rutosan – Etikett Wasch- und Reinigungspaste</title>
<link href="https://fonts.googleapis.com/css2?family=Source+Sans+3:wght@400;600&display=swap" rel="stylesheet">
<style>
  :root {
    --navy: #0a2c40;
    --red: #e30613;
    --ink: #1c1c1c;
    --icon-fill: #d6d6d6;
    --icon-line: #5f5f5f;
    --art-light: #e3f1f8;
    --art-mid: #bfe0f1;
    --page: #ffffff;
  }
  * { margin: 0; padding: 0; box-sizing: border-box; }
  html, body {
    width: 848px; height: 1200px; overflow: hidden;
    background: var(--page);
    font-family: "Source Sans 3", sans-serif;
  }
  .label {
    position: absolute;
    left: 97px; top: 86px;
    width: 664px; height: 574px;
    background: var(--page);
    box-shadow: 0 24px 60px rgba(0,0,0,0.22);
    overflow: hidden;
  }
  .key-art {
    position: absolute;
    left: 33px; top: 133px;
    width: 230px; height: 386px;
    border-radius: 6px;
    background: linear-gradient(180deg, var(--art-light), var(--art-mid));
  }
  .brand {
    position: absolute;
    left: 48px; top: 44px;
    display: flex; align-items: center; gap: 12px;
    z-index: 2;
  }
  .brand-dot {
    width: 22px; height: 22px; border-radius: 50%;
    background: var(--red);
  }
  .brand-name {
    font-size: 40px; font-weight: 400; letter-spacing: 1px;
    color: var(--navy); line-height: 1;
  }
  .intro {
    position: absolute;
    left: 359px; top: 39px; width: 230px;
    font-size: 11.6px; line-height: 15.6px; color: var(--ink);
    white-space: nowrap;
  }
  .product-name {
    position: absolute;
    right: 67px; top: 245px;
    font-size: 132px; font-weight: 600; letter-spacing: 0;
    color: var(--navy); line-height: 1;
    z-index: 2;
  }
  .product-type {
    position: absolute;
    right: 67px; top: 373px;
    font-size: 21.5px; font-weight: 400;
    color: var(--red); line-height: 1;
    white-space: nowrap;
    z-index: 2;
  }
  .usage-icons {
    position: absolute;
    left: 290px; top: 507px;
    display: flex; gap: 12px;
  }
  .usage-icon {
    width: 42px; height: 44px;
    border: 1.5px solid var(--icon-line);
    border-radius: 7px;
    background: var(--icon-fill);
  }
  .usage-icon svg { width: 100%; height: 100%; display: block; }
</style>
</head>
<body>
<main class="label">
  <div class="key-art" role="img" aria-label="Aquarell-Wassertropfen in hellblauen Tönen"></div>

  <div class="brand">
    <span class="brand-dot"></span>
    <span class="brand-name">KAVIMOR</span>
  </div>

  <p class="intro">Lorem ipsum dolor sit amet, consectetuer<br>adipiscing elit, sed diam nonummy nibh<br>euisLorem ipsum dolor sit amet, consecte-<br>tuer adipiscing elit, sed diam nonummy<br>nibh euismod tincidunt ut laoreet dolore<br>magna aliquam erat volutpat. Ut wisi enim</p>

  <h1 class="product-name">RUTOSAN</h1>
  <p class="product-type">Wasch-/Reinigungspaste . Schmierseife</p>

  <div class="usage-icons">
    <div class="usage-icon" title="Geschirr und Oberflächen">
      <svg viewBox="0 0 41 43" fill="none" stroke="var(--icon-line)" stroke-width="1.6">
        <path d="M7 22 h16 l-2 14 h-12 z" fill="#fff"/>
        <path d="M9 22 a6 5 0 0 1 12 0"/>
        <path d="M24 8 l9 3 -3 12 -9 -3 z" fill="#fff"/>
      </svg>
    </div>
    <div class="usage-icon" title="Fahrzeuge">
      <svg viewBox="0 0 41 43">
        <path d="M7 22 l4 -8 h19 l4 8 v9 h-27 z" fill="var(--icon-line)"/>
        <rect x="13" y="16" width="15" height="5" fill="var(--icon-fill)"/>
        <circle cx="12" cy="25" r="2" fill="var(--icon-fill)"/>
        <circle cx="29" cy="25" r="2" fill="var(--icon-fill)"/>
      </svg>
    </div>
    <div class="usage-icon" title="Haushalt">
      <svg viewBox="0 0 41 43">
        <path d="M5 20 l15.5 -13 15.5 13" fill="none" stroke="var(--icon-line)" stroke-width="2"/>
        <path d="M10 19 h21 v17 h-21 z" fill="var(--icon-line)"/>
        <rect x="17" y="27" width="7" height="9" fill="var(--icon-fill)"/>
      </svg>
    </div>
    <div class="usage-icon" title="pH-Wert">
      <svg viewBox="0 0 41 43" font-family="Source Sans 3, sans-serif" font-size="7" fill="var(--icon-line)">
        <text x="7" y="11">0</text>
        <text x="7" y="23">7</text>
        <text x="5" y="35">14</text>
        <line x1="20" y1="6" x2="20" y2="36" stroke="var(--icon-line)" stroke-width="1.6"/>
        <circle cx="20" cy="27" r="2"/>
        <text x="25" y="36">pH</text>
      </svg>
    </div>
    <div class="usage-icon" title="1 Esslöffel auf 10 Liter">
      <svg viewBox="0 0 41 43" font-family="Source Sans 3, sans-serif">
        <path d="M11 7 l7 8" stroke="var(--icon-line)" stroke-width="1.6"/>
        <ellipse cx="19" cy="16" rx="2.5" ry="1.6" fill="var(--icon-line)"/>
        <path d="M8 19 h25 l-3 16 h-19 z" fill="var(--icon-line)"/>
        <text x="20.5" y="31" font-size="8" font-weight="600" fill="#fff" text-anchor="middle">10 l</text>
      </svg>
    </div>
    <div class="usage-icon" title="Böden">
      <svg viewBox="0 0 41 43" fill="none" stroke="var(--icon-line)" stroke-width="1.6">
        <path d="M5 22 h16 l-2 14 h-12 z" fill="#fff"/>
        <path d="M7 22 a6 5 0 0 1 12 0"/>
        <path d="M33 6 l-7 26"/>
        <path d="M23 32 h8 l-1 4 h-9 z" fill="var(--icon-line)"/>
      </svg>
    </div>
  </div>
</main>
</body>
</html>
```